Landing Page and Logo for Auto-Blogging Platform

I created a platform that allows users to start a blog for their business, hobby, charity, etc. I need a landing page where users can learn about the platform, benefits of consistent blogging, SEO value, plans/pricing, etc. The landing page needs to have multiple call to action buttons encouraging the visitor to register/sign up for a free trial.

In addition to the landing page, I need a page for users to establish the settings for their blog. This page should be a fairly simple form, intended for the user to enter a few details to set up their blog:
1. Name of Blog
2. Up to 10 topics and/or keywords the blog should focus on
3. Theme: Color-scheme and logo upload for blog.

I have attached the specifications of the platform's functionality so you can better understand how it works, plans/pricing, etc.

I also need a logo for the business. The name of the platform is PostNook.

Target Market(s)

Website owners, bloggers, business owners

Industry/Entity Type

Technology, Internet, web design

Coding

Coded - Design and coding required

Number of Pages Required

2 page

Colors
0054AA
0677BA
7BADD7
CADEEF
E8F1F8
0094D4
00A9DD
6FCCEA
C7EBF8
E9F6FB

Requirements
Must have
• Eye-catching design but fairly light on content (keep it simple and brief.)
Nice to have
• Eye-catching yet simple design, clean and easy to understand what we are offering.
Should not have
• Too much “wordy” and confusing content.

```html
<!DOCTYPE html>
<html lang="en">
<head>
<meta charset="utf-8">
<title>PostNook – Automated Blogging Platform</title>
<link href="https://fonts.googleapis.com/css2?family=Lato:ital,wght@0,400;0,700;0,900;1,700&family=Lexend:wght@400;500;600;700&display=swap" rel="stylesheet">
<style>
:root{
  --blue-deep:#0054AA;
  --blue:#0677BA;
  --blue-mid:#7BADD7;
  --blue-pale:#CADEEF;
  --blue-mist:#E8F1F8;
  --ink:#1b1b24;
  --text:#333;
  --white:#fff;
}
*{box-sizing:border-box;margin:0;padding:0}
html,body{width:1200px;height:2738px;overflow:hidden}
body{position:relative;font-family:'Lato',sans-serif;color:var(--text);background:var(--white)}
.abs{position:absolute}
a{color:inherit;text-decoration:none}

/* top bar */
.topbar{left:0;top:0;width:1200px;height:68px;background:var(--blue)}
.mail{left:341px;top:18px;display:flex;align-items:center;gap:16px;color:#fff;font-size:15px;white-space:nowrap}
.icon-circle{width:32px;height:32px;border-radius:50%;background:#fff;display:flex;align-items:center;justify-content:center}
.socials{left:610px;top:18px;display:flex;gap:6px}
.socials span{width:32px;height:32px;border-radius:50%;background:#fff;display:block}
.search{left:808px;top:13px;width:281px;height:42px;background:#fff;border:2px solid #fff;display:flex}
.search .btn{width:42px;height:100%;background:var(--blue);display:flex;align-items:center;justify-content:center}
.search .field{padding-left:26px;line-height:38px;font-family:'Lexend',sans-serif;font-size:14px;color:#444}

/* nav */
.brand-box{left:110px;top:0;width:135px;height:136px;background:#fff}
.brand{left:110px;top:82px;font-family:'Lato',sans-serif;font-weight:700;font-size:33px;color:var(--blue);letter-spacing:-.3px}
.nav{left:340px;top:90px;font-size:16px;color:#222}
.nav a{position:absolute;white-space:nowrap}
.nav .active{color:var(--blue)}
.nav .active::before{content:"";position:absolute;left:0;top:-6px;width:50px;height:2px;background:var(--blue)}
.contact-btn{left:960px;top:85px;width:128px;height:35px;background:var(--blue-deep);color:#fff;font-weight:700;font-size:16px;text-align:center;line-height:35px}

/* hero */
.hero{left:0;top:136px;width:1200px;height:625px;background:linear-gradient(90deg,#1c2127 0%,#2c3440 40%,#4d5a68 70%,#6a7888 100%)}
.hero-title{left:110px;top:330px;color:#fff;font-family:'Lexend',sans-serif;font-weight:600;white-space:nowrap}
.hero-title small{font-size:34px}
.hero-title b{font-size:46px;margin-left:10px}
.hero-copy{left:110px;top:402px;width:530px;color:#fff;font-size:17px;line-height:31px}
.hero-btn{left:110px;top:519px;width:245px;height:46px;background:#fff;color:var(--blue-deep);font-weight:900;font-size:16px;text-align:center;line-height:46px}

/* about */
.about{left:0;top:761px;width:1200px;height:506px;background:linear-gradient(100deg,#fbeff0 0%,#fff 30%,#fff 70%,#eaf2f9 100%)}
.about-photo{left:110px;top:826px;width:400px;height:441px;background:linear-gradient(180deg,#e9e3df,#c8d6e4);border-radius:200px 200px 0 0}
.section-title{font-family:'Lexend',sans-serif;font-weight:600;color:var(--ink);white-space:nowrap}
.section-title small{font-size:32px}
.section-title b{font-size:40px;color:var(--blue-deep);margin-left:12px}
.about-title{left:598px;top:846px}
.about-lead{left:598px;top:909px;width:470px;font-size:21px;font-weight:700;line-height:33px;color:#2d2d2d}
.about-copy{left:598px;top:1025px;width:490px;font-size:16px;line-height:31px;color:#444}
.btn-blue{background:var(--blue-deep);color:#fff;font-weight:900;font-size:16px;text-align:center}
.about-btn{left:598px;top:1175px;width:166px;height:40px;line-height:40px}

/* methods */
.methods{left:0;top:1267px;width:1200px;height:432px;background:linear-gradient(90deg,#0a4fa6 0%,#0c57ad 55%,#2a67b4 75%,#6f8fb8 100%)}
.methods-photo{left:617px;top:1267px;width:583px;height:432px;background:linear-gradient(90deg,rgba(12,87,173,0) 0%,rgba(198,200,205,.55) 40%,rgba(214,196,172,.7) 100%)}
.methods-title{left:110px;top:1325px;color:#fff}
.methods-title small,.methods-title b{color:#fff}
.method-list{left:110px;top:1400px;width:560px;list-style:none;color:#fff;font-size:17px}
.method-list li{position:absolute;left:0;white-space:nowrap}
.method-list svg{position:absolute;left:0;top:4px}
.method-list .t{margin-left:46px}
.reg-btn{left:110px;top:1589px;width:167px;height:41px;background:#fff;color:var(--blue-deep);font-weight:900;font-size:16px;text-align:center;line-height:41px}

/* pricing */
.pricing-title{left:0;top:1755px;width:1200px;text-align:center}
.plan{background:#fff;box-shadow:0 2px 14px rgba(0,0,0,.09);text-align:center}
.plan h3{font-family:'Lexend',sans-serif;font-weight:600;font-size:29px;color:var(--blue-deep);letter-spacing:.3px;white-space:nowrap}
.plan .period{font-style:italic;font-weight:700;font-size:14px;color:#333;margin-top:10px}
.plan .price{font-family:'Lexend',sans-serif;font-weight:600;font-size:31px;color:var(--blue-deep);margin-top:8px}
.plan .price span{font-size:22px}
.plan hr{border:0;border-top:1px solid #999;margin:18px 0 0}
.plan p{font-size:15px;line-height:26px;color:#333;margin-top:14px;padding:0 28px}
.plan .cta{display:inline-block;width:126px;height:31px;line-height:31px;background:var(--blue-deep);color:#fff;font-weight:700;font-size:15px;margin-top:16px}
.plan-base{left:184px;top:1873px;width:282px;height:313px;padding-top:32px}
.plan-ultimate{left:733px;top:1873px;width:282px;height:313px;padding-top:32px}
.plan-premium{left:451px;top:1840px;width:295px;height:328px;padding-top:30px;background:var(--blue-deep);border-radius:4px;box-shadow:0 4px 20px rgba(0,60,130,.25)}
.plan-premium h3,.plan-premium .period,.plan-premium .price,.plan-premium p{color:#fff}
.plan-premium p{padding:0 36px}
.plan-premium hr{border-top-color:rgba(255,255,255,.6)}
.plan-premium .cta{background:#fff;color:var(--blue-deep);font-weight:400}

/* footer */
.footer{left:0;top:2272px;width:1200px;height:466px;background:var(--blue-deep)}
.f-brand{left:110px;top:2328px;font-weight:700;font-size:34px;color:#fff}
.f-sep{left:351px;top:2330px;width:2px;height:40px;background:#fff}
.f-news{left:381px;top:2334px;font-family:'Lexend',sans-serif;font-weight:600;font-size:24px;color:#fff;white-space:nowrap}
.f-input{left:694px;top:2321px;width:190px;height:48px;border:1px solid #fff;font-family:'Lexend',sans-serif;font-size:11px;color:#fff;padding-left:10px;line-height:46px}
.f-sub{left:902px;top:2321px;width:185px;height:48px;background:#fff;color:var(--blue-deep);font-family:'Lexend',sans-serif;font-weight:500;font-size:17px;display:flex;align-items:center;justify-content:space-between;padding:0 20px}
.f-rule{left:110px;width:980px;height:1px;background:rgba(255,255,255,.55)}
.f-col{color:#fff}
.f-col h4{font-family:'Lexend',sans-serif;font-weight:600;font-size:25px;letter-spacing:.8px;color:#fff;white-space:nowrap}
.f-col ul{list-style:none;margin-top:18px;font-family:'Lexend',sans-serif;font-size:16px;letter-spacing:1.2px;color:#fff}
.f-col li{height:34.5px;white-space:nowrap}
.f-contact li{display:flex;align-items:center;gap:16px;height:41px}
.f-copy{left:0;top:2700px;width:1200px;text-align:center;font-family:'Lexend',sans-serif;font-size:16px;color:#fff}
</style>
</head>
<body>

<!-- header -->
<div class="abs topbar"></div>
<div class="abs mail">
  <span class="icon-circle"><svg width="18" height="14" viewBox="0 0 18 14"><rect x="0" y="0" width="18" height="14" rx="2" fill="#0677BA"/><path d="M1 2 L9 8 L17 2" stroke="#fff" stroke-width="1.8" fill="none"/></svg></span>
  <span>hello@postnook.io</span>
</div>
<div class="abs socials" aria-label="Social links"><span></span><span></span><span></span><span></span></div>
<div class="abs search">
  <div class="btn"><svg width="18" height="18" viewBox="0 0 18 18"><circle cx="7.5" cy="7.5" r="5.5" stroke="#fff" stroke-width="2.4" fill="none"/><line x1="11.5" y1="11.5" x2="16.5" y2="16.5" stroke="#fff" stroke-width="2.6" stroke-linecap="round"/></svg></div>
  <div class="field">Search......</div>
</div>

<div class="abs brand-box"></div>
<div class="abs brand">PostNook</div>
<nav class="abs nav">
  <a class="active" style="left:0">Home</a>
  <a style="left:85px">About Us</a>
  <a style="left:193px">Our Benifits</a>
  <a style="left:320px">Subscription plan</a>
  <a style="left:485px">Latest Blog</a>
</nav>
<a class="abs contact-btn">CONTACT</a>

<!-- hero -->
<section class="abs hero" role="img" aria-label="Photo of two colleagues discussing work at an office table"></section>
<h1 class="abs hero-title"><small>WELCOME TO</small><b>POSTNOOK.</b></h1>
<p class="abs hero-copy">Lorem ipsum dolor sit amet, consectetur adipiscing elit, sed do eiusmod tempor incididunt ut labore et dolore magna aliqua. Ut enim ad minim veniam.</p>
<a class="abs hero-btn">SIGN UP FOR A FREE TRIAL</a>

<!-- about -->
<section class="abs about"></section>
<div class="abs about-photo" role="img" aria-label="Photo of a surprised woman holding an open laptop showing analytics charts"></div>
<h2 class="abs section-title about-title"><small>ABOUT</small><b>US</b></h2>
<p class="abs about-lead">The purpose of this platform is to allow anyone to start a blog and automate the process&nbsp; of creating content and posting it to the blog</p>
<p class="abs about-copy">Lorem ipsum dolor sit amet, consectetur adipiscing elit, sed do eiusmod tempor incididunt ut labore et dolore magna aliqua. Ut enim ad minim veniam, quis nostrud exercitation ullamco laboris nisi ut aliquip ex ea commodo consequat.</p>
<a class="abs btn-blue about-btn">READ MORE</a>

<!-- methods -->
<section class="abs methods"></section>
<div class="abs methods-photo" role="img" aria-label="Photo of a smiling businesswoman working on a laptop"></div>
<h2 class="abs section-title methods-title"><small>OUR</small><b>METHODS</b></h2>
<ul class="abs method-list">
  <li style="top:0"><svg width="22" height="12" viewBox="0 0 22 12"><path d="M0 6 H19 M14 1 L20 6 L14 11" stroke="#fff" stroke-width="2.4" fill="none"/></svg><span class="t">The user enters them into a table manually.</span></li>
  <li style="top:47px"><svg width="22" height="12" viewBox="0 0 22 12"><path d="M0 6 H19 M14 1 L20 6 L14 11" stroke="#fff" stroke-width="2.4" fill="none"/></svg><span class="t">The user uploads a list of blog topics in CSV format.</span></li>
  <li style="top:94px"><svg width="22" height="12" viewBox="0 0 22 12"><path d="M0 6 H19 M14 1 L20 6 L14 11" stroke="#fff" stroke-width="2.4" fill="none"/></svg><span class="t">AI can create the list of blog topics based on a prompt such as:</span></li>
  <li style="top:125px">“Provide a list of 52&nbsp; blog topics for a handyman business’s blog.”</li>
</ul>
<a class="abs reg-btn">REGISTER</a>

<!-- pricing -->
<h2 class="abs section-title pricing-title"><small>OUR</small><b>PRICING</b></h2>
<div class="abs plan plan-base">
  <h3>BASE PLAN</h3>
  <div class="period">Every month:</div>
  <div class="price">$9.99<span>/mo.</span></div>
  <hr>
  <p>1 blog post (up to 2,000 words) every month:</p>
  <a class="cta">Learn More</a>
</div>
<div class="abs plan plan-ultimate">
  <h3>ULTIMATE PLAN</h3>
  <div class="period">Every month:</div>
  <div class="price">$24<span>/mo.</span></div>
  <hr>
  <p>1 blog post per day plus unlimited manual&nbsp; posting</p>
  <a class="cta">Learn More</a>
</div>
<div class="abs plan plan-premium">
  <h3>PREMIUM PLAN</h3>
  <div class="period">Every week:</div>
  <div class="price">$14.99<span>/mo.</span></div>
  <hr>
  <p>1 blog post (up to 2,000 words) every week;</p>
  <a class="cta">Learn More</a>
</div>

<!-- footer -->
<footer class="abs footer"></footer>
<div class="abs f-brand">PostNook</div>
<div class="abs f-sep"></div>
<div class="abs f-news">Newsletter Subscription</div>
<div class="abs f-input">Enter Your E-mail</div>
<a class="abs f-sub">SUBSCRIBE <svg width="18" height="14" viewBox="0 0 18 14"><rect width="18" height="14" rx="2" fill="#0054AA"/><path d="M1 2 L9 8 L17 2" stroke="#fff" stroke-width="1.8" fill="none"/></svg></a>
<div class="abs f-rule" style="top:2407px"></div>

<div class="abs f-col" style="left:113px;top:2440px">
  <h4>CONTACT US</h4>
  <ul class="f-contact" style="margin-top:22px">
    <li><svg width="12" height="17" viewBox="0 0 12 17"><path d="M6 0 C2.7 0 0 2.6 0 5.9 C0 10 6 17 6 17 C6 17 12 10 12 5.9 C12 2.6 9.3 0 6 0Z" fill="#fff"/><circle cx="6" cy="6" r="2.3" fill="#0054AA"/></svg>United States, PostNook.</li>
    <li><svg width="16" height="16" viewBox="0 0 16 16"><path d="M3 0 L6 4 L4.5 6 C5.5 8 8 10.5 10 11.5 L12 10 L16 13 L14 16 C7 15.5 0.5 9 0 2Z" fill="#fff"/></svg>+1 555 014 2290</li>
    <li><svg width="19" height="14" viewBox="0 0 19 14"><rect width="19" height="14" rx="2" fill="#fff"/><path d="M1 2 L9.5 8 L18 2" stroke="#0054AA" stroke-width="1.8" fill="none"/></svg>support@postnook.io</li>
  </ul>
</div>
<div class="abs f-col" style="left:546px;top:2440px">
  <h4>QUICK LINKS</h4>
  <ul><li>Terms of Service</li><li>Returns Policy</li><li>Our Products</li><li>Contact</li><li>Privacy Policy</li></ul>
</div>
<div class="abs f-col" style="left:927px;top:2440px">
  <h4>ABOUT INFO</h4>
  <ul><li>Home</li><li>About Us</li><li>Our Benifits</li><li>Subscription plan</li><li>Latest Blog</li></ul>
</div>
<div class="abs f-rule" style="top:2682px"></div>
<p class="abs f-copy">Copyright © 2024 PostNook. All rights reserved.</p>

</body>
</html>
```